Modern Business Card

Modern professional business card with more than just logo and demographic info. Something memorable.

We are a trendy/modern chiropractic group with an emphasis on neurology, hence the minimalist-type brain logo. We want to convey that modern and technical aspect with professionalism and the elite nature of our practice environment.

```html
<!DOCTYPE html>
<html lang="en">
<head>
<meta charset="utf-8">
<title>Synapse Spine Care — Business Card</title>
<link rel="stylesheet" href="https://fonts.googleapis.com/css2?family=Lora:wght@600;700&family=Montserrat:wght@400;500&display=swap">
<style>
  :root {
    --brand-blue: #4680c2;
    --card-white: #ffffff;
    --mist: #f1f5f9;
    --ink: #4a4a4a;
    --ink-dark: #1e1e1e;
    --stage: #d9dadc;
  }
  * { box-sizing: border-box; margin: 0; padding: 0; }
  html, body { width: 1200px; height: 901px; overflow: hidden; }
  body {
    background: var(--stage);
    display: flex; flex-direction: column; align-items: center; justify-content: center;
    gap: 40px;
    font-family: "Montserrat", sans-serif;
  }
  .card {
    position: relative;
    width: 620px; height: 354px;
    box-shadow: 0 6px 18px rgba(0,0,0,.18);
    overflow: hidden;
  }
  .card--front {
    background: var(--brand-blue);
    display: flex; align-items: center; justify-content: center;
  }
  .brand {
    display: flex; align-items: center; gap: 14px;
    font-family: "Lora", serif; font-weight: 700;
    letter-spacing: .06em; text-transform: uppercase;
  }
  .brand__mark { width: 22px; height: 22px; border-radius: 50%; }
  .card--front .brand { color: var(--card-white); font-size: 38px; }
  .card--front .brand__mark { background: var(--card-white); width: 30px; height: 30px; }

  .card--back { background: var(--card-white); }
  .backdrop {
    position: absolute; left: 70px; top: 120px; width: 360px; height: 234px;
    border-radius: 40px 40px 0 0;
    background: linear-gradient(160deg, var(--mist) 0%, #f6f9fb 60%, rgba(246,249,251,0) 100%);
  }
  .card--back .brand {
    position: absolute; left: 330px; top: 58px;
    color: var(--ink-dark); font-size: 20px; gap: 10px;
  }
  .card--back .brand__mark { background: var(--brand-blue); }
  .contact-list {
    position: absolute; left: 342px; top: 118px;
    list-style: none; font-size: 13px; color: var(--ink); line-height: 1.7;
  }
  .contact-list li { display: flex; align-items: center; gap: 8px; }
  .contact-list svg { width: 11px; height: 11px; fill: var(--brand-blue); flex: none; }
  .address {
    position: absolute; left: 361px; top: 232px;
    font-size: 13px; color: var(--ink); line-height: 1.45; font-style: normal;
  }
  .holder { position: absolute; left: 44px; top: 248px; }
  .holder__name {
    font-family: "Lora", serif; font-weight: 700; font-size: 22px;
    color: var(--brand-blue); letter-spacing: .03em; text-transform: uppercase;
  }
  .holder__role { font-size: 14px; color: var(--ink); margin-top: 2px; }
  .accent-bar {
    position: absolute; left: 0; top: 262px; width: 10px; height: 44px;
    background: var(--brand-blue);
  }
</style>
</head>
<body>
  <section class="card card--front" aria-label="Card front">
    <div class="brand"><span class="brand__mark"></span>Synapse Spine Care</div>
  </section>

  <section class="card card--back" aria-label="Card back">
    <div class="backdrop" role="img" aria-label="Faint decorative brand pattern in pale blue-grey"></div>

    <div class="brand"><span class="brand__mark"></span>Synapse Spine Care</div>

    <ul class="contact-list">
      <li><svg viewBox="0 0 24 24"><path d="M6.6 10.8a15 15 0 0 0 6.6 6.6l2.2-2.2a1 1 0 0 1 1-.25 11.4 11.4 0 0 0 3.6.6 1 1 0 0 1 1 1V20a1 1 0 0 1-1 1A17 17 0 0 1 3 4a1 1 0 0 1 1-1h3.5a1 1 0 0 1 1 1c0 1.25.2 2.450.6 3.6a1 1 0 0 1-.25 1z"/></svg>+120 5400 1187</li>
      <li><svg viewBox="0 0 24 24"><path d="M7 1h10a2 2 0 0 1 2 2v18a2 2 0 0 1-2 2H7a2 2 0 0 1-2-2V3a2 2 0 0 1 2-2zm0 3v14h10V4z"/></svg>+965 8500 2741</li>
      <li><svg viewBox="0 0 24 24"><path d="M2 5h20v14H2zm2 2v.5l8 5 8-5V7z"/></svg>info@synapsespinecare.com</li>
      <li><svg viewBox="0 0 24 24"><path d="M12 2a10 10 0 1 0 0 20 10 10 0 0 0 0-20zm0 2c1.2 1.4 2 3.5 2.2 6H9.8c.2-2.5 1-4.6 2.2-6zM4.1 11h3.7c.1 2 .6 3.9 1.4 5.4A8 8 0 0 1 4.1 11zm0-2a8 8 0 0 1 5.1-5.4C8.4 5.1 7.9 7 7.8 9zm5.7 2h4.4c-.2 2.5-1 4.6-2.2 6-1.2-1.4-2-3.5-2.2-6zm6.4 0h3.7a8 8 0 0 1-5.1 5.4c.8-1.5 1.3-3.4 1.4-5.4zm0-2c-.1-2-.6-3.9-1.4-5.4A8 8 0 0 1 19.9 9z"/></svg>www.synapsespinecare.com</li>
    </ul>

    <address class="address">12 Marlow Lane Greenfield,<br>Riverton, 2041</address>

    <span class="accent-bar"></span>
    <div class="holder">
      <p class="holder__name">Daniel Marsh</p>
      <p class="holder__role">Senior Partner</p>
    </div>
  </section>
</body>
</html>
```